BOLD & MINIMALIST DESIGN NEEDED

We want a very bold but minimalistic business card design that is impactful and utilizes both sides of the business card. Our current logo is included for your use.

We want bold fonts and good use of negative space. We don't want the logo to overpower the design.

Target Market(s)

Professionals who are building new commercial buildings.

Industry/Entity Type

Construction

Contact Information for Business Card

Name, Title, email, office phone, cell phone, website

Font styles to use
Serif
Sans Serif

Requirements
Must have
• Bold design!

```html
<!DOCTYPE html>
<html lang="en">
<head>
<meta charset="utf-8">
<title>Ridgeline Design + Build — Business Card</title>
<link rel="stylesheet" href="https://fonts.googleapis.com/css2?family=Poppins:wght@400;500;600;700&display=swap">
<style>
  :root {
    --stage: #2b2b2b;
    --card-dark: #1c1c1c;
    --card-light: #ffffff;
    --ink: #111111;
    --ink-soft: #2a2a2a;
    --accent: #7bc043;
    --muted: #9a9a9a;
  }
  * { box-sizing: border-box; margin: 0; padding: 0; }
  html, body {
    width: 1200px; height: 875px; overflow: hidden;
    background: var(--stage);
    font-family: "Poppins", sans-serif;
  }
  .canvas { position: relative; width: 1200px; height: 875px; }

  .card {
    position: absolute;
    width: 525px; height: 300px;
    border-radius: 22px;
    overflow: hidden;
  }

  /* Back side */
  .card--back {
    left: 70px; top: 130px;
    background: var(--card-dark);
    display: flex; align-items: center; justify-content: center;
  }
  .brand {
    display: flex; align-items: center; gap: 14px;
  }
  .brand__mark {
    width: 34px; height: 34px; background: var(--accent);
  }
  .brand__text { display: flex; flex-direction: column; }
  .brand__name {
    font-weight: 700; font-size: 46px; line-height: 1;
    letter-spacing: 1px; color: var(--card-light);
  }
  .brand__tagline {
    font-weight: 700; font-size: 15px; letter-spacing: 8px;
    color: var(--card-light); margin-top: 8px;
    border-top: 1.5px solid var(--card-light); padding-top: 6px;
  }

  /* Front side */
  .card--front {
    left: 605px; top: 445px;
    background: var(--card-light);
    padding: 34px 40px;
  }
  .card--front .brand__mark { width: 22px; height: 22px; }
  .card--front .brand { gap: 10px; }
  .card--front .brand__name { font-size: 28px; color: var(--ink); }
  .card--front .brand__tagline {
    font-size: 9px; letter-spacing: 5px; color: var(--ink);
    border-top-color: var(--ink); margin-top: 5px; padding-top: 4px;
  }

  .person {
    position: relative;
    margin-top: 22px; padding-left: 14px;
  }
  .person::before {
    content: ""; position: absolute; left: -40px; top: 4px;
    width: 14px; height: 36px; background: var(--accent);
  }
  .person__name {
    font-weight: 600; font-size: 21px; line-height: 1.1; color: var(--accent);
  }
  .person__title {
    font-weight: 500; font-size: 12px; color: var(--ink-soft);
  }
  .address {
    margin-top: 10px; padding-left: 14px;
    font-size: 12px; font-weight: 500; line-height: 1.35; color: var(--ink-soft);
  }
  .contacts {
    list-style: none; margin-top: 10px; padding-left: 14px;
  }
  .contacts li {
    display: flex; align-items: center; gap: 8px;
    font-size: 12px; font-weight: 500; line-height: 1.45; color: var(--ink-soft);
  }
  .contacts svg { width: 11px; height: 11px; fill: var(--accent); flex: none; }
</style>
</head>
<body>
<main class="canvas">

  <section class="card card--back" aria-label="Card back">
    <div class="brand">
      <span class="brand__mark"></span>
      <div class="brand__text">
        <span class="brand__name">RIDGELINE</span>
        <span class="brand__tagline">DESIGN + BUILD</span>
      </div>
    </div>
  </section>

  <section class="card card--front" aria-label="Card front">
    <div class="brand">
      <span class="brand__mark"></span>
      <div class="brand__text">
        <span class="brand__name">RIDGELINE</span>
        <span class="brand__tagline">DESIGN + BUILD</span>
      </div>
    </div>

    <div class="person">
      <p class="person__name">Daniel Carter</p>
      <p class="person__title">Head contractor</p>
    </div>

    <p class="address">1420 Cedar Hollow Rd.<br>Pine Ridge, GA 30500</p>

    <ul class="contacts">
      <li>
        <svg viewBox="0 0 24 24"><path d="M6.6 10.8a15 15 0 0 0 6.6 6.6l2.2-2.2c.3-.3.7-.4 1-.2 1.1.4 2.3.6 3.6.6.6 0 1 .4 1 1V20c0 .6-.4 1-1 1A17 17 0 0 1 3 4c0-.6.4-1 1-1h3.5c.6 0 1 .4 1 1 0 1.3.2 2.5.6 3.6.1.3 0 .7-.2 1z"/></svg>
        555.210.4400
      </li>
      <li>
        <svg viewBox="0 0 24 24"><path d="M7 1h10a2 2 0 0 1 2 2v18a2 2 0 0 1-2 2H7a2 2 0 0 1-2-2V3a2 2 0 0 1 2-2zm0 3v14h10V4zm5 15.5a1.2 1.2 0 1 0 0 2.4 1.2 1.2 0 0 0 0-2.4z"/></svg>
        555-210-4401
      </li>
      <li>
        <svg viewBox="0 0 24 24"><path d="M2 5h20v14H2zm2 2v.5l8 5 8-5V7l-8 5z"/></svg>
        info@ridgeline-db.com
      </li>
      <li>
        <svg viewBox="0 0 24 24"><path d="M12 2a10 10 0 1 0 0 20 10 10 0 0 0 0-20zm0 2c1 1.3 1.8 3 2.1 5H9.9C10.2 7 11 5.3 12 4zM4.3 11h3.6c0 1 .1 2 .3 3H5a8 8 0 0 1-.7-3zm5.6 0h4.2c0 1-.1 2-.3 3h-3.6c-.2-1-.3-2-.3-3zm6.2 0h3.6c0 1-.3 2-.7 3h-3.2c.2-1 .3-2 .3-3zM12 20c-1-1.3-1.7-2.8-2-4h4c-.3 1.2-1 2.7-2 4z"/></svg>
        www.ridgeline-db.com
      </li>
    </ul>
  </section>

</main>
</body>
</html>
```